Clear Plastic Card Design

I am looking to have a business card designed from my logo icon. I am looking to match the style of a different business card I have attached in the files.
Looking for a card that is plastic, with layers of transparency in the shape of my logo icon (also attached in the files) - not a circle like the other card. The winning design will incorporate the red icon logo on the front and back and include the charity's name, "Light for the Weary Souls" in the same or similar font, as well as an email and phone number. For now, use the email: email@lightfortheweary-mail.org and the phone number 555-382-7194.
We like how the sample business card has transparency, partial and full opacity layers and a matching color scheme. Files will need to be in vector so that our business card printing company can work with it.
UPDATE:
We've some excellent designs in, thank you everyone! I got an early review from the owner, and he requested a minor redirect to find his perfect design. He wants the design to stand out by NOT being a rectangle. Try instead a circle, square, or best yet - something that falls in the outline of the logo icon, either fully or partially. Thank you, everyone!
Light for the Weary Souls text should be incorporated as well as a phone and email.

```html
<!DOCTYPE html>
<html lang="en">
<head>
<meta charset="utf-8">
<title>Light for the Weary Souls – Card</title>
<link href="https://fonts.googleapis.com/css2?family=Questrial&display=swap" rel="stylesheet">
<style>
  :root {
    --crimson: #c4082f;
    --rose: #d81b4a;
    --orange: #f07000;
    --ink: #111111;
    --paper: #ffffff;
    --backdrop: #e4e4e4;
  }
  html, body {
    margin: 0;
    width: 1175px;
    height: 1200px;
    overflow: hidden;
    background: var(--backdrop);
    font-family: "Questrial", "Helvetica Neue", Arial, sans-serif;
  }
  .card {
    position: absolute;
    left: 70px;
    top: 71px;
    width: 1035px;
    height: 1058px;
    background: var(--paper);
    border-radius: 46px;
    overflow: hidden;
  }
  .card-shapes {
    position: absolute;
    inset: 0;
  }
  .charity-name {
    position: absolute;
    left: 85px;
    top: 98px;
    margin: 0;
    color: var(--paper);
    font-weight: 400;
    font-size: 100px;
    line-height: 112px;
    letter-spacing: 0.5px;
  }
  .contact-list {
    position: absolute;
    left: 110px;
    top: 598px;
    margin: 0;
    padding: 0;
    list-style: none;
  }
  .contact-item {
    display: flex;
    align-items: center;
    height: 54px;
    color: var(--ink);
    font-size: 33px;
  }
  .contact-icon {
    width: 42px;
    height: 42px;
    margin-right: 18px;
    flex: none;
  }
  .brand-mark {
    position: absolute;
    left: 760px;
    top: 740px;
    width: 240px;
    margin: 0;
    color: var(--crimson);
    font-size: 46px;
    line-height: 52px;
    text-align: right;
  }
</style>
</head>
<body>
  <div class="card">
    <svg class="card-shapes" width="1035" height="1058" viewBox="0 0 1035 1058" aria-hidden="true">
      <defs>
        <linearGradient id="band-header" x1="0" y1="0" x2="1" y2="0">
          <stop offset="0" stop-color="var(--crimson)"/>
          <stop offset="0.3" stop-color="var(--rose)"/>
          <stop offset="0.55" stop-color="var(--orange)"/>
          <stop offset="0.8" stop-color="var(--rose)"/>
          <stop offset="1" stop-color="var(--crimson)"/>
        </linearGradient>
        <radialGradient id="band-footer" cx="0.5" cy="0.6" r="0.55">
          <stop offset="0" stop-color="var(--orange)"/>
          <stop offset="0.55" stop-color="var(--rose)"/>
          <stop offset="1" stop-color="var(--crimson)"/>
        </radialGradient>
        <linearGradient id="bar-accent" x1="0" y1="0" x2="0" y2="1">
          <stop offset="0" stop-color="var(--crimson)"/>
          <stop offset="0.5" stop-color="var(--orange)"/>
          <stop offset="1" stop-color="var(--rose)"/>
        </linearGradient>
        <linearGradient id="corner-piece" x1="0" y1="0" x2="0" y2="1">
          <stop offset="0" stop-color="var(--orange)"/>
          <stop offset="1" stop-color="var(--crimson)"/>
        </linearGradient>
      </defs>
      <polygon class="header-band" points="35,74 736,74 955,345 35,345" fill="url(#band-header)"/>
      <rect class="contact-bar" x="51" y="593" width="11" height="171" fill="url(#bar-accent)"/>
      <polygon class="corner-piece" points="0,840 62,793 62,938 0,938" fill="url(#corner-piece)"/>
      <polygon class="footer-band" points="0,938 984,938 897,1058 0,1058" fill="url(#band-footer)"/>
    </svg>

    <h1 class="charity-name">Light for the<br>Weary Souls</h1>

    <ul class="contact-list">
      <li class="contact-item">
        <svg class="contact-icon" viewBox="0 0 24 24" aria-hidden="true">
          <circle cx="12" cy="12" r="12" fill="var(--ink)"/>
          <path d="M8.2 6.2c.5-.4 1.1-.3 1.4.2l1.1 1.9c.3.5.2 1-.2 1.4l-.8.7c.6 1.4 1.7 2.6 3.1 3.2l.7-.8c.4-.4 1-.5 1.4-.2l1.9 1.1c.5.3.6 1 .2 1.4l-.9 1c-.6.6-1.5.8-2.3.5-3-1.1-5.4-3.5-6.5-6.5-.3-.8-.1-1.7.5-2.3z" fill="var(--paper)"/>
        </svg>
        555-382-7194
      </li>
      <li class="contact-item">
        <svg class="contact-icon" viewBox="0 0 24 24" aria-hidden="true">
          <circle cx="12" cy="12" r="12" fill="var(--ink)"/>
          <rect x="6" y="8" width="12" height="8.5" rx="1" fill="none" stroke="var(--paper)" stroke-width="1.6"/>
          <path d="M6.5 8.6 12 12.8l5.5-4.2" fill="none" stroke="var(--paper)" stroke-width="1.6"/>
        </svg>
        email@lightfortheweary-mail.org
      </li>
      <li class="contact-item">
        <svg class="contact-icon" viewBox="0 0 24 24" aria-hidden="true">
          <circle cx="12" cy="12" r="12" fill="var(--ink)"/>
          <circle cx="12" cy="12" r="6" fill="none" stroke="var(--paper)" stroke-width="1.8"/>
          <path d="M9 9.5c1.5 0 2 1 1.5 2s.5 2 1.5 2.5M14 8c-.5 1 0 2 1.2 2.3" fill="none" stroke="var(--paper)" stroke-width="1.5"/>
        </svg>
        www.lightfortheweary-web.org
      </li>
    </ul>

    <p class="brand-mark">Light for the Weary Souls</p>
  </div>
</body>
</html>
```